Fern Acupuncture Business Card Design

I would like a business card design for my acupuncture business which is based from 2 practices in Melbourne, Australia.

The front of the card should include:

*The Logo
* Name - Miranda Tesselhoff (B.App.Sc.(TCM), Dip.Rem.Mass.). (I would like the letters after my name in slightly smaller font)
* Mobile number - 0472 318 604
* Web address - www.fernacupuncture.com.au

On the back of the card I would somehow like to fit my 2 clinic addresses in. They are:

The Calm & Balance Rooms
842 Pellam St, Camberwell VIC 3124
Ph: 1300 287 419

Riverbend Natural Therapies & Herbal Practice
19 Quillon Ave, Malvern East VIC 3145
Ph: (03) 9731 4052

If there is space, I'd also like to add to the back of the card - Next Appointment............................ (or something along those lines).

Thanks and happy designing!

Target Market(s)

Health consumers, and colleagues in the health industry

Industry/Entity Type

Clinic

Contact Information for Business Card

as above in brief

Requirements
Must have
• I've seen some ok designs coming in, however I'd like to avoid the generic look with the added curved line details etc. I don't particularly need extra patterns added to the card. I'd prefer it to look quite clean and simple, and using more earthy colours (I'm not super keen on the lime green that a lot of designs seem to include. I don't mind the full black or white look, (obviously the back side needs to be a lighter colour to allow me to write appointment details on it). I also quite like the idea of the background looking like brown recycled paper (just an idea - that's not 100% necessary).
Nice to have
• I have an idea that I could have the main flower part of the logo printed as metallic.
Should not have
• Generic patterns and too much added detail.

```html
<!DOCTYPE html>
<html lang="en">
<head>
<meta charset="utf-8">
<title>Fern Acupuncture Business Card</title>
<link rel="stylesheet" href="https://fonts.googleapis.com/css2?family=Cinzel:wght@700&family=Arimo:wght@400;700&display=swap">
<style>
  :root {
    --backdrop: #5e5a55;
    --card: #f1eadb;
    --ink: #2b2520;
    --ink-soft: #4a4038;
    --mark: #2b2520;
    --mark-accent: #a9824f;
    --mark-accent-deep: #7a5a33;
  }
  * { box-sizing: border-box; margin: 0; padding: 0; }
  html, body { width: 1200px; height: 960px; overflow: hidden; }
  body {
    background: var(--backdrop);
    display: flex;
    align-items: center;
    justify-content: center;
    gap: 80px;
    font-family: "Arimo", Arial, sans-serif;
    color: var(--ink);
  }
  .card {
    width: 420px;
    height: 700px;
    background: var(--card);
    position: relative;
    box-shadow: 0 10px 30px rgba(0,0,0,.35);
  }
  /* brand mark */
  .brand {
    display: flex;
    flex-direction: column;
    align-items: center;
    gap: 14px;
  }
  .brand-dot {
    border-radius: 50%;
    background: radial-gradient(circle at 35% 35%, var(--mark-accent), var(--mark-accent-deep));
  }
  .brand-name {
    font-family: "Arimo", Arial, sans-serif;
    font-weight: 700;
    color: var(--mark);
    letter-spacing: .08em;
    text-transform: uppercase;
  }
  /* front */
  .card-front .brand { position: absolute; top: 70px; left: 0; right: 0; }
  .card-front .brand-dot { width: 150px; height: 150px; }
  .card-front .brand-name { font-size: 22px; }
  .front-details {
    position: absolute;
    left: 50px;
    right: 40px;
    top: 380px;
  }
  .practitioner-name {
    font-family: "Cinzel", Georgia, serif;
    font-weight: 700;
    font-size: 30px;
    letter-spacing: .02em;
    line-height: 1.1;
  }
  .credentials {
    font-size: 13px;
    color: var(--ink-soft);
    margin-top: 8px;
  }
  .contact { margin-top: 50px; font-size: 19px; line-height: 1.9; }
  /* back */
  .card-back .brand { position: absolute; top: 40px; right: 40px; gap: 8px; }
  .card-back .brand-dot { width: 80px; height: 80px; }
  .card-back .brand-name { font-size: 12px; }
  .appointment {
    position: absolute;
    top: 170px;
    left: 36px;
    right: 36px;
  }
  .appointment-label { font-weight: 700; font-size: 20px; }
  .write-line {
    border-bottom: 3px dotted var(--ink);
    height: 42px;
  }
  .clinics {
    position: absolute;
    top: 330px;
    left: 30px;
    right: 30px;
    text-align: center;
  }
  .clinic + .clinic { margin-top: 40px; }
  .clinic-name { font-weight: 700; font-size: 20px; line-height: 1.25; }
  .clinic-line { font-size: 16px; line-height: 1.6; }
</style>
</head>
<body>
  <section class="card card-front">
    <div class="brand">
      <span class="brand-dot"></span>
      <span class="brand-name">Fern Acupuncture</span>
    </div>
    <div class="front-details">
      <h1 class="practitioner-name">Miranda Tesselhoff</h1>
      <p class="credentials">B.App.Sc.(TCM), Dip.Rem.Mass.</p>
      <div class="contact">
        <p>0472 318 604</p>
        <p>www.fernacupuncture.com.au</p>
      </div>
    </div>
  </section>

  <section class="card card-back">
    <div class="brand">
      <span class="brand-dot"></span>
      <span class="brand-name">Fern Acupuncture</span>
    </div>
    <div class="appointment">
      <p class="appointment-label">Next Appointment :-</p>
      <div class="write-line"></div>
      <div class="write-line"></div>
    </div>
    <div class="clinics">
      <div class="clinic">
        <p class="clinic-name">The Calm &amp; Balance Rooms</p>
        <p class="clinic-line">842 Pellam St, Camberwell VIC 3124</p>
        <p class="clinic-line">1300 287 419</p>
      </div>
      <div class="clinic">
        <p class="clinic-name">Riverbend Natural Therapies &amp;<br>Herbal Practice</p>
        <p class="clinic-line">19 Quillon Ave, Malvern East VIC 3145</p>
        <p class="clinic-line">(03) 9731 4052</p>
      </div>
    </div>
  </section>
</body>
</html>
```